Yoga Workshop - Yoga Practice information flyer

I am a yoga teacher who will be presenting a workshop on yoga for sleep and need a brochure for my clients which outlines a practice that I give them so they can do the practice at home. Ideally I would like a brochure that is a single A3 size of paper in size that folds in half to an A4 booklet with the entire practice on the centre section to make it easy for people to do the practice at home with just one open page in front of them:
* Front page detailing "Yoga for Sleep Workshop" and "Restorative Yoga Practice"
* Centre contains the information on the practice contained in the attached word document. The practice consists of 5 postures, so there needs to be five separate sections which have the pictures of the postures (attached in uploaded files) and the wording contained in the attached word document. All pictures uploaded need to be included in the flyer as each posture has different pictures demonstrating the posture using yoga props or using things people have at home
* Back page containing a picture of myself (picture uploaded in files) with some information about me (contained in the attached word document) and my website www.calmdrift.com.au

I also need this flyer to be able to printed on 2 double sided A4 sheets of paper so will require 2 x pdf file versions. Importantly, for the centre section of the flyer, the design needs to ensure if it is printed on A4 paper, the wording and pictures for each of the postures are not separated over two pages

Target Market(s)

Existing clients

Requirements
Must have
• Detailed in project description
Nice to have
• The word document also contains some quotes. These do not need to be included in the flyer. If there is room and there is room for one or two of those please include where it would look good
Should not have
• Stock pictures of people in yoga postures which a normal everyday person could not get into

```html
<!DOCTYPE html>
<html lang="en">
<head>
<meta charset="utf-8">
<title>Restorative Yoga Practice – Postures 3 to 5</title>
<link rel="stylesheet" href="https://fonts.googleapis.com/css2?family=Josefin+Sans:ital,wght@0,400;0,600;0,700;1,600;1,700&display=swap">
<style>
  :root {
    --terracotta: #cf8966;
    --navy: #34485f;
    --ink: #2f4159;
    --white: #ffffff;
    --photo-wood: #8a4a26;
    --photo-wall: #e9e7e4;
    --photo-mat: #1f8fc0;
  }
  * { margin: 0; padding: 0; box-sizing: border-box; }
  html, body { width: 848px; height: 1200px; overflow: hidden; background: var(--white); }
  body { font-family: "Josefin Sans", sans-serif; color: var(--ink); }
  .page { position: relative; width: 848px; height: 1200px; overflow: hidden; background: var(--white); }

  .band { position: absolute; left: 0; top: 340px; width: 848px; height: 550px; }

  .photo {
    position: absolute;
    width: 168px;
    height: 260px;
    border: 5px solid var(--terracotta);
    background: linear-gradient(180deg, var(--photo-wall) 0%, var(--photo-wall) 22%, var(--photo-wood) 23%, #a65a2e 60%, var(--photo-mat) 61%, var(--photo-mat) 100%);
  }
  .photo--navy { border-color: var(--navy); }
  .photo--white { border-color: var(--white); }
  .photo--tall { height: 211px; }

  .posture { position: absolute; font-size: 14px; line-height: 15.7px; }
  .posture__title {
    color: var(--terracotta);
    font-weight: 700;
    font-size: 20px;
    line-height: 24px;
    letter-spacing: 0.6px;
    margin-bottom: 12px;
  }
  .posture p { margin-bottom: 15.5px; }
  .label { color: var(--terracotta); font-weight: 700; font-style: italic; }

  .posture--three { left: 382px; top: 28px; width: 440px; }
  .posture--four { left: 43px; top: 652px; width: 760px; color: var(--white); }
  .posture--five { left: 382px; top: 912px; width: 440px; }
</style>
</head>
<body>
<main class="page">

  <svg class="band" viewBox="0 0 848 550" aria-hidden="true">
    <path d="M0 7 Q424 38 848 7 L848 543 Q424 512 0 543 Z" fill="var(--navy)"/>
  </svg>

  <!-- Posture 3 -->
  <div class="photo" style="left:19px; top:43px;" role="img" aria-label="Woman lying on a yoga mat with legs up the wall, hips on a bolster"></div>
  <div class="photo photo--navy" style="left:195px; top:43px;" role="img" aria-label="Woman lying with legs up the wall, hips supported on a folded towel"></div>
  <section class="posture posture--three">
    <h2 class="posture__title">Posture 3 – Elevated Legs-Up-the-Wall Pose</h2>
    <p><span class="label">Props</span> – 1 x bolsters (or towel or blanket densely folded to a width of about 15-30cm), 1 x cushion for head support (optional)</p>
    <p><span class="label">Set up notes</span> – To enter the posture sit at 90 degrees to the wall with the side of your hip about a hand width away from the wall, and the bolster/folded towel or blanket close by. Lie down on the mat on your side then roll onto your back and extend feet up wall. The feet can push into the wall to elevate the hips slightly so the bolster/folded towel or blanket can slide underneath the hips. The prop should be positioned underneath the sacrum (flat bony structure at the base of the spine).</p>
    <p><span class="label">Caution</span> – If any lower back pain is experience adjust the height the hips are elevated by using a towel or blanket that is folded to a lower height.</p>
  </section>

  <!-- Posture 4 -->
  <div class="photo photo--white photo--tall" style="left:42px; top:412px;" role="img" aria-label="Supported child's pose on a bolster, seen from behind"></div>
  <div class="photo photo--tall" style="left:290px; top:412px;" role="img" aria-label="Supported child's pose resting the head on a bolster, side view"></div>
  <div class="photo photo--white photo--tall" style="left:543px; top:412px;" role="img" aria-label="Supported child's pose on stacked bed pillows"></div>
  <section class="posture posture--four">
    <h2 class="posture__title">Posture 4 – Supported Child’s Pose</h2>
    <p><span class="label">Props</span> – 1-2 x bolsters (or 3-4 bed pillows)</p>
    <p><span class="label">Set up notes</span> – Position bolster or stacked pillows under torso. Rest the head in one direction and remember to turn to the head to the other side half way through the time you spend in this posture.</p>
    <p><span class="label">Caution</span> – This position may not be suitable for people with limited hip and knee mobility. Increasing the height of the support, by adding bolsters, folded blankets or pillows, will increase the angle of knees and hip. Additional cushioning may be required under the knees if too much pressure on the knees is experienced. If pain is experienced in this posture, omit this position from your practice.</p>
  </section>

  <!-- Posture 5 -->
  <div class="photo" style="left:19px; top:913px;" role="img" aria-label="Woman reclining on her back with a bolster under the knees"></div>
  <div class="photo photo--navy" style="left:195px; top:913px;" role="img" aria-label="Woman reclining on her back with a bed pillow under the knees"></div>
  <section class="posture posture--five">
    <h2 class="posture__title">Posture 5 – Basic Relaxation Posture with Knee Support</h2>
    <p><span class="label">Props</span> – 1 x bolsters (or 1 x bed pillows or rolled up towel)</p>
    <p><span class="label">Set up notes</span> – Reclining on back, position bolster or pillows under knees.</p>
  </section>

</main>
</body>
</html>
```